New Bicycle shop business card

Hi!
I'm looking for a business card for my new proffesional bike mechanics shop. This shop is only for fixing broken bikes and not selling bikes.
Peferbly a modern and sleek and modern design.
Colors: black, grey, red, white
Information:
Name: Rijwielwerkplaats Vanhoutte
Shop owner: Bart Vanhoutte & Marieke Segers
Website: www.rijwielwerkplaats-vanhoutte.be
Email: info@rijwielwerkplaats-vanhoutte.be
Phone number: +32471902368
Street adres: Kerkweg 46
9940 Bellebeke
Slogan/shop information: Herstellingen van alle merken.
Logo: see files.
Target Market(s)
People who seek a mechanic to fix or upgrade their bikes.
Contact Information for Business Card
Information:
Website: info@rijwielwerkplaats-vanhoutte.be
9940 Bellebeke
Logo: see files.

```html
<!DOCTYPE html>
<html lang="nl">
<head>
<meta charset="utf-8">
<title>Rijwielwerkplaats Vanhoutte – visitekaartje</title>
<link rel="stylesheet" href="https://fonts.googleapis.com/css2?family=Montserrat:wght@700;800&family=Roboto:wght@400;500&display=swap">
<style>
  :root {
    --backdrop: #3a3a3a;
    --card-black: #1f1f21;
    --brand-red: #dc2b3b;
    --steel-grey: #8d8f93;
    --white: #ffffff;
  }
  * { box-sizing: border-box; margin: 0; padding: 0; }
  html, body { width: 799px; height: 1200px; overflow: hidden; }
  body {
    background: var(--backdrop);
    font-family: "Roboto", Arial, sans-serif;
    color: var(--white);
    position: relative;
  }
  .card {
    position: absolute;
    left: 119.5px;
    width: 560px;
    height: 350px;
    border-radius: 22px;
    background: var(--card-black);
    overflow: hidden;
    box-shadow: 0 10px 30px rgba(0,0,0,.45);
  }
  .card--front { top: 115px; }
  .card--back { top: 700px; }

  /* front */
  .front-name {
    position: absolute;
    inset: 0;
    display: flex;
    flex-direction: column;
    align-items: center;
    justify-content: center;
    font-family: "Montserrat", Arial, sans-serif;
    font-weight: 800;
    font-size: 26px;
    line-height: 1.15;
    letter-spacing: 1px;
    text-transform: uppercase;
    color: var(--steel-grey);
    text-align: center;
  }

  /* back */
  .back-bands { position: absolute; inset: 0; }
  .wordmark {
    position: absolute;
    top: 22px;
    left: 30px;
    font-family: "Montserrat", Arial, sans-serif;
    font-weight: 800;
    color: var(--white);
    text-transform: uppercase;
    line-height: 1.05;
  }
  .wordmark__line1 { font-size: 26px; letter-spacing: 0.5px; }
  .wordmark__line2 { font-size: 15px; letter-spacing: 9px; }

  .contact { position: absolute; top: 120px; left: 30px; }
  .contact__name {
    font-family: "Montserrat", Arial, sans-serif;
    font-weight: 700;
    font-size: 17px;
    letter-spacing: .5px;
    text-transform: uppercase;
  }
  .contact__role { font-size: 11px; margin-bottom: 8px; }
  .contact__row {
    display: flex;
    align-items: center;
    gap: 8px;
    font-size: 12.5px;
    height: 19px;
  }
  .contact__icon { width: 12px; height: 12px; flex: none; }
  .contact__row--plain { padding-left: 20px; }

  .slogan {
    position: absolute;
    left: 30px;
    top: 300px;
    font-size: 14px;
  }

  .band-name {
    position: absolute;
    left: 330px;
    top: 205px;
    width: 210px;
    display: flex;
    align-items: center;
    gap: 10px;
    font-family: "Montserrat", Arial, sans-serif;
    font-weight: 800;
    font-size: 15px;
    line-height: 1.15;
    text-transform: uppercase;
    color: var(--white);
  }
  .band-name__square {
    width: 14px; height: 14px; flex: none;
    background: var(--white);
  }
</style>
</head>
<body>

  <section class="card card--front" aria-label="Voorkant visitekaartje">
    <div class="front-name">
      <span>Rijwielwerkplaats</span>
      <span>Vanhoutte</span>
    </div>
  </section>

  <section class="card card--back" aria-label="Achterkant visitekaartje">
    <svg class="back-bands" viewBox="0 0 560 350" aria-hidden="true">
      <rect x="0" y="108" width="310" height="172" fill="var(--brand-red)"/>
      <rect x="310" y="185" width="250" height="95" fill="var(--brand-red)"/>
    </svg>

    <div class="wordmark">
      <div class="wordmark__line1">Rijwielwerkplaats</div>
      <div class="wordmark__line2">Vanhoutte</div>
    </div>

    <div class="contact">
      <div class="contact__name">Marieke Segers</div>
      <div class="contact__role">Owner</div>
      <div class="contact__row">
        <svg class="contact__icon" viewBox="0 0 12 12"><path d="M2 1h2.5l1 3-1.5 1a6 6 0 0 0 3 3l1-1.5 3 1V11A9.5 9.5 0 0 1 1 2z" fill="#fff"/></svg>
        <span>+32471902368</span>
      </div>
      <div class="contact__row">
        <svg class="contact__icon" viewBox="0 0 12 12"><rect x="0.5" y="2" width="11" height="8" fill="#fff"/><path d="M.5 2 6 6.5 11.5 2" fill="none" stroke="var(--brand-red)" stroke-width="1"/></svg>
        <span>www.rijwielwerkplaats-vanhoutte.be</span>
      </div>
      <div class="contact__row">
        <svg class="contact__icon" viewBox="0 0 12 12"><circle cx="6" cy="6" r="5.5" fill="#fff"/><path d="M.5 6h11M6 .5c-3 3-3 8 0 11M6 .5c3 3 3 8 0 11" fill="none" stroke="var(--brand-red)" stroke-width=".8"/></svg>
        <span>info@rijwielwerkplaats-vanhoutte.be</span>
      </div>
      <div class="contact__row contact__row--plain">
        <span>Kerkweg 46 9940 Bellebeke</span>
      </div>
    </div>

    <div class="band-name">
      <span class="band-name__square"></span>
      <span>Rijwielwerkplaats<br>Vanhoutte</span>
    </div>

    <p class="slogan">Herstellingen van alle merken</p>
  </section>

</body>
</html>
```